VTMB site redesign

Please redesign a home page with content provided. PSD only - no coding
Can use any images from Snapwelder.com

Please create a site design that more clearly illustrates the client's services and expertise. We are looking for a high-end design.

Any images used must be generic or of Dallas TX.

Fonts: Any
Colors: Match to logo
Look: Modern - Professional

Target Market(s)

medium-large business owners

Number of Pages Required

1 page

Font styles to use
Serif
Sans Serif

Requirements
Must have
• cohesive professional design
• high end look
• Match to logo

```html
<!DOCTYPE html>
<html lang="en">
<head>
<meta charset="utf-8">
<title>VTMB Commercial Realty</title>
<link href="https://fonts.googleapis.com/css2?family=Lato:wght@400;700&family=Roboto:wght@400;500;700&display=swap" rel="stylesheet">
<style>
:root{
  --red:#b00008;
  --red-deep:#8a0006;
  --ink:#1c1c1c;
  --text:#555;
  --grey-bg:#e6e6e6;
  --footer:#2b2b2b;
  --white:#fff;
}
*{box-sizing:border-box;margin:0;padding:0}
html,body{width:1200px;height:3488px;overflow:hidden;background:var(--white)}
body{position:relative;font-family:'Lato',sans-serif;color:var(--ink)}
.abs{position:absolute}
h1,h2,h3{font-family:'Roboto',sans-serif;font-weight:500}

/* header */
.site-header{position:absolute;top:0;left:0;width:1200px;height:125px;background:var(--white);z-index:3}
.brand{position:absolute;left:122px;top:20px;display:flex;align-items:center;gap:14px}
.brand-square{width:56px;height:56px;background:var(--red)}
.brand-name{font-family:'Lato',sans-serif;font-weight:700;font-size:24px;color:var(--ink);line-height:1.15;letter-spacing:1px}
.phone-tab{position:absolute;left:795px;top:0;width:265px;height:42px;background:var(--red);color:var(--white);font-weight:700;font-size:19px;display:flex;align-items:center;justify-content:center;gap:8px;border-radius:0 0 4px 4px}
.main-nav{position:absolute;top:72px;left:457px;display:flex;gap:0}
.main-nav a{font-family:'Lato',sans-serif;font-size:16px;color:var(--ink);text-decoration:none;margin-right:52px;letter-spacing:.3px}

/* hero */
.hero{position:absolute;top:125px;left:0;width:1200px;height:645px;overflow:hidden}
.hero-photo{position:absolute;inset:0;background:linear-gradient(160deg,#9bb3cc 0%,#4d6b8c 35%,#23364f 70%,#1a2a40 100%)}
.hero-title{position:absolute;top:195px;width:1200px;text-align:center;color:var(--white);font-family:'Roboto',sans-serif;font-weight:700;font-size:46px;line-height:1.08}
.hero-sub{position:absolute;top:293px;width:1200px;text-align:center;color:var(--white);font-size:21px;line-height:1.45}
.hero-dots{position:absolute;top:528px;left:552px;display:flex;gap:8px}
.hero-dots span{width:13px;height:13px;border-radius:50%;background:var(--white);border:2px solid var(--white)}
.hero-dots span.open{background:transparent}
.hero-curve{position:absolute;left:0;bottom:0}

/* why */
.section-title{position:absolute;width:1200px;text-align:center;font-size:28px;letter-spacing:.5px}
.feature{position:absolute;width:460px;height:120px}
.feature-icon{position:absolute;left:0;top:0;width:92px;height:84px;border:2px solid var(--red);display:flex;align-items:center;justify-content:center}
.feature h3{position:absolute;left:125px;top:0;font-family:'Lato',sans-serif;font-weight:700;font-size:17px}
.feature p{position:absolute;left:125px;top:28px;width:330px;font-size:12.5px;line-height:1.75;color:var(--text)}
.cta-text{position:absolute;top:1254px;width:1200px;text-align:center;font-size:23px;line-height:1.45}
.btn{position:absolute;top:1335px;left:492px;width:213px;height:45px;background:var(--red);color:var(--white);font-family:'Roboto',sans-serif;font-weight:700;font-size:15px;display:flex;align-items:center;justify-content:center}

/* team */
.team{position:absolute;top:1463px;left:0;width:1200px;height:600px;background:var(--grey-bg)}
.team-notch{position:absolute;top:1463px;left:575px}
.team-intro{position:absolute;top:1573px;left:238px;width:724px;text-align:center;font-size:13px;line-height:2.05;color:#444}
.member{position:absolute;top:1700px;width:260px;text-align:center}
.member-photo{width:200px;height:200px;border-radius:50%;margin:0 auto}
.member-name{margin-top:20px;color:var(--red);font-weight:700;font-size:16px}
.member-role{margin-top:6px;font-size:14px;color:var(--text);line-height:1.45}

/* testimonials */
.testimonial-text{position:absolute;top:2200px;left:282px;width:636px;text-align:center;color:var(--white);font-size:17px;line-height:1.78}
.quote-mark{position:absolute;top:2178px;color:var(--white);font-family:'Roboto',sans-serif;font-weight:700;font-size:96px;line-height:1}
.client-name{position:absolute;top:2373px;width:1200px;text-align:center;color:var(--white);font-weight:700;font-size:18px}
.t-dots{position:absolute;top:2447px;left:556px;display:flex;gap:6px;align-items:center}
.t-dots .arrow{width:19px;height:19px;border-radius:50%;background:var(--white)}
.t-dots .dot{width:8px;height:8px;border-radius:50%;border:1px solid var(--white)}
.t-dots .dot.on{background:var(--white)}

/* articles */
.articles-title{position:absolute;top:2608px;left:116px;font-size:26px}
.card{position:absolute;top:2660px;width:303px;height:345px;border:1px solid #cfcfcf;background:var(--white)}
.card-photo{height:198px}
.card-date{position:absolute;top:169px;left:87px;width:128px;height:30px;background:var(--red);color:var(--white);font-size:14px;display:flex;align-items:center;justify-content:center}
.card h3{margin-top:22px;text-align:center;font-size:18px;font-weight:400}
.card p{margin:8px auto 0;width:212px;text-align:center;font-size:11px;line-height:1.6;color:var(--text)}
.card .more{display:block;margin-top:8px;text-align:center;color:var(--red);font-weight:700;font-size:11px}

/* footer */
.site-footer{position:absolute;top:3095px;left:0;width:1200px;height:393px;background:var(--footer);color:var(--white)}
.foot-col{position:absolute;top:3187px}
.foot-col h4{font-family:'Roboto',sans-serif;font-weight:500;font-size:17px;letter-spacing:.5px;line-height:1.15}
.foot-links{list-style:none;margin-top:22px}
.foot-links li{font-size:14px;line-height:31px}
.contact-row{display:flex;gap:12px;font-size:14px;line-height:1.9;margin-top:8px}
.contact-row svg{flex:none;margin-top:5px}
.social{display:flex;gap:8px;margin-top:18px}
.social span{width:38px;height:38px;border:2px solid var(--white);border-radius:50%}
.notice{font-size:11.5px;text-decoration:underline;margin-top:16px;line-height:1.4}
.copyright{position:absolute;top:3388px;left:716px;font-size:12px;color:#aaa}
</style>
</head>
<body>

<header class="site-header">
  <div class="brand"><span class="brand-square"></span><span class="brand-name">VTMB<br>COMMERCIAL REALTY</span></div>
  <div class="phone-tab">
    <svg width="16" height="16" viewBox="0 0 24 24"><path fill="#fff" d="M6.6 10.8a15 15 0 0 0 6.6 6.6l2.2-2.2a1 1 0 0 1 1-.25 11.4 11.4 0 0 0 3.6.57 1 1 0 0 1 1 1V20a1 1 0 0 1-1 1A17 17 0 0 1 3 4a1 1 0 0 1 1-1h3.5a1 1 0 0 1 1 1c0 1.25.2 2.45.57 3.57a1 1 0 0 1-.25 1z"/></svg>
    Call Today: 214-555-0148
  </div>
  <nav class="main-nav"><a>SERVICES</a><a>ABOUT VTMB</a><a>CONTACT US</a><a>BLOG</a><a>MARKET NEWS</a></nav>
</header>

<section class="hero">
  <div class="hero-photo" role="img" aria-label="Glass office towers seen from below against a blue cloudy sky"></div>
  <h1 class="hero-title">PROFESSIONAL OFFICE AND<br>WAREHOUSE LEASING</h1>
  <p class="hero-sub">Fast-track your search with tenant reps that only serve<br>you, and specialize in the DFW area.</p>
  <div class="hero-dots"><span class="open"></span><span></span><span></span><span></span></div>
  <svg class="hero-curve" width="1200" height="120" viewBox="0 0 1200 120">
    <path d="M0 120 L0 50 Q600 -10 1200 70 L1200 120 Z" fill="var(--red)"/>
    <path d="M0 120 L0 62 Q600 4 1200 82 L1200 120 Z" fill="#fff"/>
  </svg>
</section>

<h2 class="section-title" style="top:800px">WHY TENANT REPRESENTATION?</h2>

<div class="feature" style="left:140px;top:900px">
  <div class="feature-icon"><svg width="56" height="56" viewBox="0 0 56 56" fill="none" stroke="#b00008" stroke-width="2"><circle cx="28" cy="12" r="6"/><circle cx="11" cy="38" r="5"/><circle cx="45" cy="38" r="5"/><path d="M20 26h16M4 52c0-5 3-8 7-8s7 3 7 8M38 52c0-5 3-8 7-8s7 3 7 8M18 40h20"/></svg></div>
  <h3>Relationships</h3>
  <p>Save time by trusting VTMB year after year to find the right location for you. Once we've worked together, we know what you need, and you can keep your budget details private.</p>
</div>
<div class="feature" style="left:642px;top:900px">
  <div class="feature-icon"><svg width="56" height="56" viewBox="0 0 56 56" fill="none" stroke="#b00008" stroke-width="2"><circle cx="38" cy="18" r="11"/><circle cx="41" cy="15" r="3"/><path d="M30 26 8 48v4h6v-5h5v-5h5l6-6"/></svg></div>
  <h3>Access to More</h3>
  <p>We have no agreements or personal incentives for specific properties, so we can always show you the offices that are right for you.</p>
</div>
<div class="feature" style="left:140px;top:1065px">
  <div class="feature-icon"><svg width="56" height="56" viewBox="0 0 56 56" fill="none" stroke="#b00008" stroke-width="3"><circle cx="28" cy="28" r="24"/><path d="M16 29l9 9 17-19"/></svg></div>
  <h3>Free To You</h3>
  <p>You pay us nothing. We get our commission from the property being leased.</p>
</div>
<div class="feature" style="left:642px;top:1065px">
  <div class="feature-icon"><svg width="56" height="56" viewBox="0 0 56 56" fill="none" stroke="#b00008" stroke-width="2"><circle cx="28" cy="28" r="9"/><path d="M28 6v7M28 43v7M6 28h7M43 28h7M12.4 12.4l5 5M38.6 38.6l5 5M12.4 43.6l5-5M38.6 17.4l5-5"/><circle cx="28" cy="28" r="16"/></svg></div>
  <h3>Customized Service</h3>
  <p>Aside from saving you the time of repeating what your needs are to each new location, we also provide a report of the places you've seen, so it's easier to share and make a decision.</p>
</div>

<p class="cta-text">If you need to find office or warehouse space in the Dallas Fort Worth area,<br>the team at VTMB has the experience you need.</p>
<a class="btn">SPACE CALCULATOR</a>

<section class="team"></section>
<svg class="team-notch" width="50" height="22" viewBox="0 0 50 22"><path d="M0 0h50L25 20Z" fill="#fff"/><path d="M17 6l8 7 8-7" fill="none" stroke="#999" stroke-width="1.5"/></svg>
<h2 class="section-title" style="top:1530px">MEET THE TEAM</h2>
<p class="team-intro">At VTMB we believe that you deserve the best professional advice and personal service with your commercial real estate negotiations. By choosing VTMB as your tenant reps in the Dallas/Fort Worth area, you will receive the assistance of accomplished and experienced commercial real estate brokers and salespeople who are licensed by the Texas Real Estate Commission to practice in Texas since 1982.</p>
<div class="member" style="left:198px"><div class="member-photo" role="img" aria-label="Portrait of the founder" style="background:radial-gradient(circle at 50% 40%,#c9a58c,#4a4a4a 75%)"></div><div class="member-name">Warren T. Mabry</div><div class="member-role">Founder and President</div></div>
<div class="member" style="left:473px"><div class="member-photo" role="img" aria-label="Portrait of the senior director" style="background:radial-gradient(circle at 50% 40%,#d8b59c,#e2e2e2 75%)"></div><div class="member-name">Owen Castellano</div><div class="member-role">Senior Director, Commercial<br>Property Specialist</div></div>
<div class="member" style="left:748px"><div class="member-photo" role="img" aria-label="Portrait of the associate" style="background:radial-gradient(circle at 50% 40%,#e0b7a0,#8fb7dc 75%)"></div><div class="member-name">Dennis Arlo Whitfield, Jr.</div><div class="member-role">Associate, Tenant Rep Specialist</div></div>

<svg class="abs" style="top:2020px;left:0" width="1200" height="540" viewBox="0 0 1200 540">
  <path d="M0 22 L1200 0 L1200 518 L0 540 Z" fill="var(--red)"/>
  <path d="M0 22 L330 52 L0 52 Z" fill="var(--red-deep)"/>
  <path d="M0 22 L600 60 L0 42 Z" fill="#6e0005" opacity=".6"/>
  <path d="M860 498 L1200 470 L1200 518 Z" fill="#c9c9c9"/>
  <path d="M960 502 L1200 486 L1200 518 Z" fill="#e4e4e4"/>
</svg>
<h2 class="section-title" style="top:2141px;color:#fff">CLIENT TESTMONIALS</h2>
<span class="quote-mark" style="left:228px">&ldquo;</span>
<span class="quote-mark" style="left:918px">&rdquo;</span>
<p class="testimonial-text">The real estate team at VTMB has decades of experience in Commercial. One advantage of VTMB is they know all the properties that are about to become available, BEFORE they are available. They have the inside track on properties and they watch your back at the negotiating table. Very impressive with a polished approach. Let the team run with your next project and you won't be disappointed</p>
<p class="client-name">Harold Jameson Pike</p>
<div class="t-dots"><span class="arrow"></span><span class="dot on"></span><span class="dot"></span><span class="dot"></span><span class="dot"></span><span class="arrow"></span></div>

<h2 class="articles-title">RECENT ARTICLES</h2>
<article class="card" style="left:115px"><div class="card-photo" role="img" aria-label="Low brick retail building under a blue sky" style="background:linear-gradient(#7fa6d6 0%,#b9cfe8 45%,#a6896a 60%,#7a7a78 100%)"></div><span class="card-date">02 Aug 2017</span><h3>Your Blog Title here</h3><p>netus et malesuada fames ac turpis egestas. Cras id elit integer quis urna ut ante enim dapibus malesuada fringilla eu cond</p><a class="more">READ MORE</a></article>
<article class="card" style="left:440px"><div class="card-photo" role="img" aria-label="Modern glass office building lit at dusk" style="background:linear-gradient(#6b76b8 0%,#a59ac8 40%,#c9a45a 65%,#5a5a60 100%)"></div><span class="card-date">02 Aug 2017</span><h3>Your Blog Title here</h3><p>netus et malesuada fames ac turpis egestas. Cras id elit integer quis urna ut ante enim dapibus malesuada fringilla eu cond</p><a class="more">READ MORE</a></article>
<article class="card" style="left:765px"><div class="card-photo" role="img" aria-label="Blue glass towers against a bright sky" style="background:linear-gradient(135deg,#e6eef7 0%,#6aa0d8 45%,#1f5fa8 100%)"></div><span class="card-date">02 Aug 2017</span><h3>Your Blog Title here</h3><p>netus et malesuada fames ac turpis egestas. Cras id elit integer quis urna ut ante enim dapibus malesuada fringilla eu cond</p><a class="more">READ MORE</a></article>

<svg class="abs" style="top:3060px;left:0" width="1200" height="60" viewBox="0 0 1200 60">
  <path d="M0 10 L300 60 L0 60 Z" fill="var(--red)"/>
  <path d="M0 30 L520 50 L1200 35 L1200 60 L0 60 Z" fill="var(--footer)"/>
</svg>
<footer class="site-footer"></footer>
<div class="foot-col" style="left:172px">
  <h4>COMPANY</h4>
  <ul class="foot-links"><li>Home</li><li>Services</li><li>About VTMB</li><li>Contact Us</li><li>Blog</li><li>Market News</li></ul>
</div>
<div class="foot-col" style="left:392px">
  <h4>CONTACT INFO</h4>
  <div class="contact-row" style="margin-top:18px"><svg width="14" height="18" viewBox="0 0 14 18"><path fill="#fff" d="M7 0a7 7 0 0 0-7 7c0 5 7 11 7 11s7-6 7-11a7 7 0 0 0-7-7zm0 10a3 3 0 1 1 0-6 3 3 0 0 1 0 6z"/></svg><span>412 Elmridge Avenue, Suite 300,<br>Dallas, TX 75201</span></div>
  <div class="contact-row"><svg width="16" height="16" viewBox="0 0 24 24"><path fill="none" stroke="#fff" stroke-width="2" d="M6.6 10.8a15 15 0 0 0 6.6 6.6l2.2-2.2 4.6 1.3V20A17 17 0 0 1 3 4h3.5l1.3 4.6z"/></svg><span>214-555-0148</span></div>
  <div class="contact-row" style="margin-top:2px"><svg width="16" height="14" viewBox="0 0 16 14"><rect x="1" y="1" width="14" height="12" fill="none" stroke="#fff" stroke-width="1.5"/><path d="M1 1l7 6 7-6" fill="none" stroke="#fff" stroke-width="1.5"/></svg><span>214-555-0193</span></div>
  <div class="social"><span></span><span></span><span></span><span></span></div>
</div>
<div class="foot-col" style="left:707px">
  <h4>TEXAS REAL ESTATE<br>COMMISSION MANDATED<br>DISCLOSURE NOTICES</h4>
  <p class="notice">Texas Real Estate Commission Information About Brokerage Services</p>
  <p class="notice" style="margin-top:12px">Texas Real Estate Commission Consumer Protection Notice</p>
</div>
<p class="copyright">© 2018 Company Name. All right reserved &nbsp;Terms of Use</p>

</body>
</html>
```